Business card for my new company (Accounting firm)

I need a business card for my new business Brightwell Advisory and Ledger SA. Our services are accounting, tax, audit and financial management. Our customers are small companies, start-ups and new companies. The final design has to show financial security, trust and growth. Please find our logo attached to the business card. Text for the business card: Brightwell Advisory and Ledger SA Tomas Varenholt Director and Founder Certified Accountant Tel. 022 418 57 34 tv@clairevalconseil.ch www.clairevalconseil.ch Rue des Vergières 27 1201 Geneva
Target Market(s)
Our customers are small companies, start-ups and new companies.
Industry/Entity Type
Finance And Accounting
Contact Information for Business Card
Claireval Conseil et Comptes SA
Tomas Varenholt
Directeur et Fondateur
Expert-comptable diplômé
Tél. 022 418 57 34
tv@clairevalconseil.ch
www.clairevalconseil.ch
Rue des Vergières 27
1201 Genève

```html
<!DOCTYPE html>
<html lang="en">
<head>
<meta charset="utf-8">
<title>Claireval Conseil et Comptes – Business Card</title>
<link href="https://fonts.googleapis.com/css2?family=Lato:wght@400;700&family=Montserrat:wght@400;500&display=swap" rel="stylesheet">
<style>
  :root {
    --backdrop: #2a2a2a;
    --paper: #ffffff;
    --ink: #2f2f2f;
    --brand-deep: #1d5e96;
    --blue-top: #2a8dcf;
    --blue-mid: #35b1e4;
    --blue-bottom: #1b67a3;
    --rule: #bdbdbd;
  }
  * { margin: 0; padding: 0; box-sizing: border-box; }
  html, body { width: 1200px; height: 1200px; overflow: hidden; background: var(--backdrop); }
  .canvas { position: relative; width: 1200px; height: 1200px; }

  .card { position: absolute; top: 310px; height: 594px; }
  .card-front { left: 234px; width: 364px; background: var(--paper); text-align: center; font-family: "Lato", sans-serif; color: var(--ink); }
  .card-back {
    left: 627px; width: 369px;
    background: linear-gradient(180deg, var(--blue-top) 0%, var(--blue-mid) 45%, var(--blue-mid) 58%, var(--blue-bottom) 100%);
  }

  .wordmark { position: absolute; left: 30px; right: 30px; font-family: "Montserrat", sans-serif; font-weight: 500; text-align: center; white-space: nowrap; }
  .card-front .wordmark { top: 214px; color: var(--ink); }
  .wordmark-name { display: block; font-size: 36px; letter-spacing: 2px; line-height: 1; }
  .wordmark-sub { display: block; margin-top: 10px; font-size: 13px; letter-spacing: 2.4px; }

  .holder { position: absolute; top: 318px; left: 0; right: 0; }
  .holder-name { color: var(--brand-deep); font-weight: 700; font-size: 22px; line-height: 28px; }
  .holder-role { font-size: 17px; line-height: 21px; }

  .contact-divider { position: absolute; top: 394px; left: 87px; width: 190px; height: 26px; }
  .contact { position: absolute; top: 428px; left: 0; right: 0; font-size: 17px; line-height: 22px; }
  .address-rule { position: absolute; top: 503px; left: 88px; width: 188px; height: 1px; background: #d6d6d6; }
  .address { position: absolute; top: 513px; left: 0; right: 0; font-size: 17px; line-height: 22px; }

  .back-decor { position: absolute; inset: 0; }
  .card-back .wordmark { top: 462px; color: #ffffff; }
  .card-back .wordmark-name { font-size: 44px; letter-spacing: 2px; }
  .card-back .wordmark-sub { margin-top: 14px; font-size: 18px; letter-spacing: 2.6px; }
</style>
</head>
<body>
<main class="canvas">

  <section class="card card-front" aria-label="Business card front">
    <div class="wordmark">
      <span class="wordmark-name">CLAIREVAL</span>
      <span class="wordmark-sub">CONSEIL ET COMPTES</span>
    </div>

    <div class="holder">
      <p class="holder-name">SA TOMAS VARENHOLT</p>
      <p class="holder-role">Director and Founder</p>
      <p class="holder-role">Certified Accountant</p>
    </div>

    <svg class="contact-divider" viewBox="0 0 190 26" aria-hidden="true">
      <line x1="0" y1="13" x2="52" y2="13" stroke="var(--rule)" stroke-width="1.2"/>
      <line x1="138" y1="13" x2="190" y2="13" stroke="var(--rule)" stroke-width="1.2"/>
      <g fill="var(--brand-deep)">
        <circle cx="67" cy="13" r="12"/>
        <circle cx="94" cy="13" r="12"/>
        <circle cx="121" cy="13" r="12"/>
      </g>
      <g fill="none" stroke="#ffffff" stroke-width="1.5" stroke-linejoin="round">
        <path d="M60 12 q7-6 14 0 l-2 2 h-10 z"/>
        <rect x="62" y="14" width="10" height="5" rx="1"/>
        <rect x="87.5" y="8.5" width="13" height="9" rx="1"/>
        <path d="M87.5 9 l6.5 5 l6.5 -5"/>
        <circle cx="121" cy="13" r="6"/>
        <path d="M115 13 h12 M121 7 q-4 6 0 12 q4 -6 0 -12"/>
      </g>
    </svg>

    <div class="contact">
      <p>022 418 57 34</p>
      <p>tv@clairevalconseil.ch</p>
      <p>www.clairevalconseil.ch</p>
    </div>
    <div class="address-rule"></div>
    <div class="address">
      <p>Rue des Vergières 27</p>
      <p>1201 Geneva</p>
    </div>
  </section>

  <section class="card card-back" aria-label="Business card back">
    <div class="back-decor" role="img" aria-label="Soft blue background where a large faint brand decoration sits"></div>
    <div class="wordmark">
      <span class="wordmark-name">CLAIREVAL</span>
      <span class="wordmark-sub">CONSEIL ET COMPTES</span>
    </div>
  </section>

</main>
</body>
</html>
```